Lantern Petals Website v.1 - attract floral shop franchisees

I need a simple information website for my new business. We are a franchisor of flower shops. The overall purpose of the website is to promote the company and the service, especially to potential franchisees and retailers. Only about 4 pages are required including homepage, About, For Supermarkets, For Franchisees, and Contact. No special functions are required except the site will have two separate inquiry forms that must be filled out online and submitted via automated email. Similarly, an email form should be linked from the Contact page. I have a logo and business cards designed by ArtMingle, and I would like the site to have a consistent color scheme and style. The key to design will be to express the joy and love associated with flowers and floral bouquets.
IMPORTANT - I will be exporting the website design to Wordpress CMS in a site hosted by HostNimbus. For smooth integration into WordPress hosted by HostNimbus, the designer should build the site using a WordPress-friendly format. Ideally, they should use HTML, CSS, and PHP. Creating a custom theme or using a page builder that exports to WordPress-compatible files is best. This ensures the site can be easily imported and managed within WordPress.

Target Market(s)

Potential franchisees (existing florists or creative types who might like to own a floral business) and supermarkets who might want us to run their floral department

Industry/Entity Type

Floral retailing

Requirements
Must have
• A brand theme that is beautiful, consistent throughout and builds on the logo design
Nice to have
• Show gender and ethnic diversity in customers and florists. Pictures of happy florists (for franchisees) and pictures of amazing floral department displays (for supermarkets)

```html
<!DOCTYPE html>
<html lang="en">
<head>
<meta charset="utf-8">
<title>Lantern Petals – Website Pages</title>
<link rel="stylesheet" href="https://fonts.googleapis.com/css2?family=Great+Vibes&family=Roboto:wght@400;500;700&display=swap">
<style>
:root{
  --green:#1f8a3c;
  --green-dark:#14722f;
  --mint:#34b57c;
  --orange:#f0ac28;
  --orange-deep:#e29a12;
  --ink:#3a3a3a;
  --muted:#777;
  --white:#fff;
  --board:#ffffff;
  --field:#9a9a9a;
}
*{box-sizing:border-box;margin:0;padding:0}
html,body{width:921px;height:1200px;overflow:hidden;background:var(--board)}
body{position:relative;font-family:"Roboto",Arial,sans-serif;color:var(--ink)}
.defs{position:absolute;width:0;height:0}
.board-label{position:absolute;font-weight:500;font-size:8px;letter-spacing:.2px;color:#2a2a2a}
.page{position:absolute;width:271px;background:var(--white);box-shadow:0 0 3px rgba(0,0,0,.18);overflow:hidden}
.page > *{position:absolute}
.hero{left:0;top:0;width:271px;height:126px}
.hero svg{display:block;width:271px;height:126px}
.logo-tab{left:25px;top:0;width:49px;height:30px;background:var(--white);display:flex;align-items:center;justify-content:center;gap:2px;box-shadow:0 0 2px rgba(0,0,0,.15)}
.logo-dot{width:5px;height:5px;border-radius:50%;background:var(--orange);flex:none}
.logo-name{font-weight:500;font-size:5.2px;line-height:5.6px;color:var(--orange)}
.menu-btn{right:24px;top:9px;width:13px;height:13px;border-radius:50%;background:var(--orange);display:flex;flex-direction:column;align-items:center;justify-content:center;gap:1.2px}
.menu-btn i{display:block;width:6px;height:.8px;background:#4a3a10}
.menu-btn i:nth-child(2){width:4px;margin-left:2px}
.hero-kicker{left:0;width:271px;text-align:center;font-weight:500;font-size:4.6px;letter-spacing:1.6px;color:var(--white)}
.hero-title{left:0;width:271px;text-align:center;font-family:"Great Vibes",cursive;color:var(--white);line-height:1;white-space:nowrap}
.copy{font-size:3.1px;line-height:4.7px;color:var(--ink)}
.copy p+p{margin-top:3.5px}
.hexes{left:0;top:0;width:271px;height:600px;pointer-events:none}
.script-head{font-family:"Great Vibes",cursive;color:var(--orange);font-size:8px;line-height:1;white-space:nowrap}
.ticks{list-style:none;font-size:3px;line-height:3.6px;color:var(--ink)}
.ticks li{position:relative;padding-left:8px;margin-bottom:3.9px}
.ticks li::before{content:"";position:absolute;left:2px;top:-.3px;width:1.8px;height:3.4px;border-right:1.1px solid var(--green);border-bottom:1.1px solid var(--green);transform:rotate(40deg)}
.pill{height:9px;border:1px solid var(--orange);border-radius:5px;font-weight:700;font-size:3px;display:flex;align-items:center;justify-content:center;background:var(--white);color:#222;white-space:nowrap}
.pill.solid{background:var(--orange);border-color:var(--orange-deep)}
.arrow{width:20px;height:8px}
.band{left:0;width:271px;height:172px}
.band svg{display:block;width:271px;height:172px}
.band-title{position:absolute;left:46px;top:95px;font-family:"Great Vibes",cursive;font-size:16px;color:var(--white);white-space:nowrap}
.band-sub{position:absolute;left:34px;top:121px;font-family:"Great Vibes",cursive;font-size:6.5px;color:var(--white);white-space:nowrap}
.band-mail{position:absolute;left:24px;top:134px;font-weight:500;font-size:6.4px;color:var(--white);white-space:nowrap}
.band-logo{position:absolute;left:160px;top:80px;width:80px;display:flex;align-items:center;justify-content:center;gap:3px}
.band-logo .logo-dot{width:9px;height:9px}
.band-logo span{font-weight:500;font-size:9px;line-height:9.5px;color:var(--orange)}
.footer{left:0;width:271px;height:48px;text-align:center}
.socials{position:absolute;top:10px;left:0;width:271px;display:flex;justify-content:center;gap:3px}
.socials i{display:block;width:5px;height:5px;border-radius:50%;background:#555}
.foot-links{position:absolute;top:22px;left:0;width:271px;font-size:3px;color:#333;word-spacing:1px}
.foot-links span{margin:0 6px}
.foot-copy{position:absolute;top:32px;left:0;width:271px;font-size:3px;color:#333}
.form-head{font-family:"Great Vibes",cursive;font-size:11px;color:var(--green);white-space:nowrap}
.form-mail{font-weight:500;font-size:5.4px;color:#222}
.form-mail b{font-weight:400;color:var(--orange)}
.field{height:10px;border:.8px solid var(--field);font-size:2.9px;color:#444;padding:0 4px;display:flex;align-items:center;background:var(--white)}
.field.tall{height:21px;align-items:flex-start;padding-top:4px}
.field .chev{margin-left:auto;width:0;height:0;border-left:1.3px solid transparent;border-right:1.3px solid transparent;border-top:1.6px solid #333}
.field .split{flex:1;text-align:center}
.field .split:first-child{text-align:left}
.box{display:inline-block;width:2.4px;height:2.4px;border:.4px solid #333;margin:0 1px 0 4px;vertical-align:middle;position:relative}
.box.on::after{content:"";position:absolute;left:.5px;top:-.1px;width:.8px;height:1.3px;border-right:.4px solid #111;border-bottom:.4px solid #111;transform:rotate(40deg)}
.thanks{font-size:3.1px;line-height:5px;color:#222}
</style>
</head>
<body>

<svg class="defs" aria-hidden="true">
  <defs>
    <linearGradient id="heroPhoto" x1="0" y1="0" x2="1" y2="1">
      <stop offset="0" stop-color="#3f9e5f"/>
      <stop offset=".5" stop-color="#2f8a4b"/>
      <stop offset="1" stop-color="#4fae6d"/>
    </linearGradient>
    <linearGradient id="bandPhoto" x1="0" y1="0" x2="1" y2="0">
      <stop offset="0" stop-color="#cfd6cf"/>
      <stop offset=".5" stop-color="#e8b3c2"/>
      <stop offset="1" stop-color="#d9a2b3"/>
    </linearGradient>
    <symbol id="hex" viewBox="0 0 38 42"><polygon points="19,0 38,10.5 38,31.5 19,42 0,31.5 0,10.5"/></symbol>
  </defs>
</svg>

<div class="board-label" style="left:24px;top:18px">ABOUT US</div>
<div class="board-label" style="left:327px;top:18px">FOR SUPERMARKETS</div>
<div class="board-label" style="left:630px;top:18px">FOR FRANCHISEES</div>
<div class="board-label" style="left:24px;top:598px">OUR GALLERY</div>
<div class="board-label" style="left:327px;top:598px">CONTACT US</div>

<!-- ABOUT US -->
<section class="page" style="left:24px;top:37px;height:534px">
  <div class="hero">
    <svg viewBox="0 0 271 126">
      <rect role="img" aria-label="Photo of roses and florist tools on a green worktable" width="271" height="126" fill="url(#heroPhoto)"/>
      <path fill="var(--orange)" d="M0 58 C80 42 170 62 271 116 L271 126 L0 126Z"/>
      <path fill="var(--white)" d="M0 104 C90 84 190 106 271 122 L271 126 L0 126Z"/>
      <path fill="var(--green)" d="M0 91 C50 77 100 80 140 97 C100 86 50 88 0 101Z"/>
    </svg>
  </div>
  <div class="logo-tab"><span class="logo-dot"></span><span class="logo-name">Lantern<br>Petals</span></div>
  <div class="menu-btn"><i></i><i></i><i></i></div>
  <div class="hero-kicker" style="top:23px">LANTERN PETALS</div>
  <div class="hero-title" style="top:28px;font-size:24px">About Us</div>

  <svg class="hexes" viewBox="0 0 271 600" role="img" aria-label="Honeycomb of photos showing smiling florists and flower displays">
    <use href="#hex" x="-18" y="113" width="38" height="42" fill="#a27a62"/>
    <use href="#hex" x="22" y="113" width="38" height="42" fill="#7f8e6a"/>
    <use href="#hex" x="0" y="152" width="38" height="42" fill="#5f7d5a"/>
    <use href="#hex" x="41" y="152" width="38" height="42" fill="#c48a5a"/>
    <use href="#hex" x="22" y="190" width="38" height="42" fill="#6b6f62"/>
    <use href="#hex" x="190" y="240" width="38" height="42" fill="#c86a78"/>
    <use href="#hex" x="230" y="240" width="38" height="42" fill="#d48a9a"/>
    <use href="#hex" x="170" y="276" width="38" height="42" fill="#8a8a52"/>
    <use href="#hex" x="211" y="276" width="38" height="42" fill="#9a5a4a"/>
  </svg>

  <div class="copy" style="left:88px;top:140px;width:160px">
    <p>Fresh flowers convey special sentiments - love, happiness, joy – which every person deserves. Lantern Petals is an entrepreneurial company created to make top quality fresh flowers and artisan-designed bouquets accessible to every consumer at affordable prices.</p>
    <p>Lantern Petals brings the best of professional florists and supermarkets together for the benefit of consumers. It supports a national network of franchisees who own and operate the floral departments of some of the country's most progressive supermarkets, selling the finest floral stems and bouquets to customers at the market's best value.</p>
    <p>Lantern Petals brings the best of professional florists and supermarkets together for the benefit of consumers. It supports a national network of owner-operator franchisees, who in many cases are multi-site professional florists, with comprehensive services to enhance franchise profits. Lantern Petals works with some of the country's largest and most progressive supermarkets to provide franchisee ownership and operation of their strategically important floral departments. Supermarkets find that Lantern Petals is able to improve their financial outcomes, provide attentive customer service and satisfaction, and lift the quality of the entire store environment, all while providing customers with the finest floral stems and bouquets at the market's best value.</p>
  </div>

  <svg style="left:37px;top:232px;width:34px;height:34px" viewBox="0 0 34 34" aria-hidden="true"><circle cx="17" cy="17" r="14" fill="#d9b56a"/></svg>

  <div class="copy" style="left:25px;top:264px;width:145px">
    <p>Lantern Petals operates in partnership with Frostvale Group, the leading franchisor of sushi stations and pre-packaged fruit and vegetable departments to supermarkets across the North America and United Kingdom. Lantern Petals' provides a combination of floral industry experience and supermarket franchising expertise that guarantees consumers, franchisees and supermarket partners each receive exceptional service and value.</p>
  </div>

  <div class="band" style="top:318px">
    <svg viewBox="0 0 271 172">
      <rect role="img" aria-label="Photo of a greenhouse full of gerbera flowers" width="271" height="110" fill="url(#bandPhoto)"/>
      <path fill="var(--orange)" d="M0 52 C70 34 140 58 175 108 C195 138 230 150 271 136 L271 172 L0 172Z"/>
      <path fill="var(--mint)" d="M0 42 C65 22 135 38 172 96 L175 108 C140 58 70 34 0 52Z"/>
      <circle cx="200" cy="88" r="45" fill="var(--white)"/>
    </svg>
    <div class="band-title">Contact Us</div>
    <div class="band-sub">For questions and further information.</div>
    <div class="band-mail">Contact: info@Lantern-Petals.com</div>
    <div class="band-logo"><span class="logo-dot"></span><span>Lantern<br>Petals</span></div>
  </div>

  <footer class="footer" style="top:486px">
    <div class="socials"><i></i><i></i><i></i><i></i><i></i></div>
    <div class="foot-links">About Us<span>|</span>For Supermarkets<span>|</span>For Franchisees<span>|</span>Our Gallery<span>|</span>Contact Us</div>
    <div class="foot-copy">Lantern Petals © 2024 All Rights Reserved | Privacy Policy | Terms and Conditions</div>
  </footer>
</section>

<!-- FOR SUPERMARKETS -->
<section class="page" style="left:327px;top:37px;height:534px">
  <div class="hero">
    <svg viewBox="0 0 271 126">
      <rect role="img" aria-label="Photo of a supermarket floral department with green bouquets" width="271" height="126" fill="url(#heroPhoto)"/>
      <path fill="var(--orange)" d="M0 58 C80 42 170 62 271 116 L271 126 L0 126Z"/>
      <path fill="var(--white)" d="M0 104 C90 84 190 106 271 122 L271 126 L0 126Z"/>
      <path fill="var(--green)" d="M0 91 C50 77 100 80 140 97 C100 86 50 88 0 101Z"/>
    </svg>
  </div>
  <div class="logo-tab"><span class="logo-dot"></span><span class="logo-name">Lantern<br>Petals</span></div>
  <div class="menu-btn"><i></i><i></i><i></i></div>
  <div class="hero-kicker" style="top:27px">LANTERN PETALS</div>
  <div class="hero-title" style="top:33px;font-size:25px">For Supermarkets</div>

  <svg class="hexes" viewBox="0 0 271 600" role="img" aria-label="Honeycomb of photos showing florists at work and bright flower stands">
    <use href="#hex" x="2" y="114" width="36" height="40" fill="#a27a62"/>
    <use href="#hex" x="41" y="114" width="36" height="40" fill="#7f8e6a"/>
    <use href="#hex" x="80" y="114" width="36" height="40" fill="#8a9a6a"/>
    <use href="#hex" x="2" y="151" width="36" height="40" fill="#5f7d5a"/>
    <use href="#hex" x="41" y="151" width="36" height="40" fill="#c48a5a"/>
    <use href="#hex" x="80" y="151" width="36" height="40" fill="#b85a7a"/>
    <use href="#hex" x="21" y="187" width="36" height="40" fill="#6b6f62"/>
    <use href="#hex" x="60" y="187" width="36" height="40" fill="#c86a78"/>
    <use href="#hex" x="41" y="223" width="36" height="40" fill="#a2564a"/>
  </svg>

  <div class="copy" style="left:133px;top:137px;width:118px">
    <p>Lantern Petals works with some of the country's largest and most progressive supermarkets to provide franchisee ownership and operation of their strategically important floral departments. Supermarkets find that Lantern Petals is able to improve their financial outcomes, provide attentive customer service and satisfaction, and lift the quality of the entire store environment.</p>
  </div>
  <div class="script-head" style="left:133px;top:182px">Opportunity for Supermarkets</div>
  <ul class="ticks" style="left:133px;top:194px;width:118px">
    <li>Enhance floral revenue streams with efficient assortments and new offerings</li>
    <li>Reduce the costs of operating a floral department</li>
    <li>Improve the quality, useful life and merchandising of floral products</li>
    <li>Provide attentive customer service, including semi-custom bouquets, by professional florist staff</li>
    <li>Maintain a beautiful, fresh and well-stocked environment</li>
    <li>Increase sales and profits</li>
    <li>Enhance the entire customer shopping environment</li>
  </ul>
  <div class="copy" style="left:25px;top:270px;width:222px">
    <p>Lantern Petals operates in partnership with Frostvale Group, a leading international, multi-channel Japanese food business and the largest franchisor of sushi stations and pre-packaged fruit and vegetable departments to supermarkets across the United States, Canada and the United Kingdom. Frostvale, working closely with its supermarket partners, has recognised that franchising sushi kiosks and select other supermarket food departments can dramatically improve financial performance for the supermarkets while creating entrepreneurial business opportunities for franchisees. It has chosen to support Lantern Petals in assisting supermarkets with a similarly compelling opportunity in floral departments. Lantern Petals' combination of floral industry experience and supermarket franchising expertise guarantees that consumers, franchisees and supermarket partners each receive exceptional service and value.</p>
  </div>

  <div class="band" style="top:318px">
    <svg viewBox="0 0 271 172">
      <rect role="img" aria-label="Photo of pink roses in a flower shop window" width="271" height="110" fill="url(#bandPhoto)"/>
      <path fill="var(--orange)" d="M0 52 C70 34 140 58 175 108 C195 138 230 150 271 136 L271 172 L0 172Z"/>
      <path fill="var(--mint)" d="M0 42 C65 22 135 38 172 96 L175 108 C140 58 70 34 0 52Z"/>
      <circle cx="200" cy="88" r="45" fill="var(--white)"/>
    </svg>
    <div class="band-title">Contact Us</div>
    <div class="band-sub">For questions and further information.</div>
    <div class="band-mail">Contact: info@Lantern-Petals.com</div>
    <div class="band-logo"><span class="logo-dot"></span><span>Lantern<br>Petals</span></div>
  </div>
  <svg class="arrow" style="left:158px;top:314px" viewBox="0 0 20 8" aria-hidden="true"><path d="M1 2 C8 2 13 4 18 6 M15 3.5 L18 6 L14.5 7" fill="none" stroke="#333" stroke-width=".7"/></svg>
  <div class="pill" style="left:183px;top:318px;width:62px">FOR FRANCHISEES QUESTIONS?</div>

  <footer class="footer" style="top:486px">
    <div class="socials"><i></i><i></i><i></i><i></i><i></i></div>
    <div class="foot-links">About Us<span>|</span>For Supermarkets<span>|</span>For Franchisees<span>|</span>Our Gallery<span>|</span>Contact Us</div>
    <div class="foot-copy">Lantern Petals © 2024 All Rights Reserved | Privacy Policy | Terms and Conditions</div>
  </footer>
</section>

<!-- FOR FRANCHISEES -->
<section class="page" style="left:630px;top:37px;height:556px">
  <div class="hero">
    <svg viewBox="0 0 271 126">
      <rect role="img" aria-label="Photo of green hydrangeas and lilac roses" width="271" height="126" fill="url(#heroPhoto)"/>
      <path fill="var(--orange)" d="M0 58 C80 42 170 62 271 116 L271 126 L0 126Z"/>
      <path fill="var(--white)" d="M0 104 C90 84 190 106 271 122 L271 126 L0 126Z"/>
      <path fill="var(--green)" d="M0 91 C50 77 100 80 140 97 C100 86 50 88 0 101Z"/>
    </svg>
  </div>
  <div class="logo-tab"><span class="logo-dot"></span><span class="logo-name">Lantern<br>Petals</span></div>
  <div class="menu-btn"><i></i><i></i><i></i></div>
  <div class="hero-kicker" style="top:27px">LANTERN PETALS</div>
  <div class="hero-title" style="top:33px;font-size:25px">For Franchisees</div>

  <div class="band" style="top:385px">
    <svg viewBox="0 0 271 172">
      <rect role="img" aria-label="Photo of pink roses in a flower shop window" width="271" height="110" fill="url(#bandPhoto)"/>
      <path fill="var(--orange)" d="M0 52 C70 34 140 58 175 108 C195 138 230 150 271 136 L271 172 L0 172Z"/>
      <path fill="var(--mint)" d="M0 42 C65 22 135 38 172 96 L175 108 C140 58 70 34 0 52Z"/>
      <circle cx="200" cy="88" r="45" fill="var(--white)"/>
    </svg>
    <div class="band-title">Contact Us</div>
    <div class="band-sub">For questions and further information.</div>
    <div class="band-mail">Contact: info@Lantern-Petals.com</div>
    <div class="band-logo"><span class="logo-dot"></span><span>Lantern<br>Petals</span></div>
  </div>
  <div style="left:0;top:380px;width:271px;height:30px;background:linear-gradient(var(--white) 50%,rgba(255,255,255,0))"></div>

  <svg class="hexes" viewBox="0 0 271 600" role="img" aria-label="Honeycomb of photos showing happy florists and their arrangements">
    <use href="#hex" x="2" y="112" width="36" height="40" fill="#a27a62"/>
    <use href="#hex" x="41" y="112" width="36" height="40" fill="#7f8e6a"/>
    <use href="#hex" x="80" y="112" width="36" height="40" fill="#8a9a6a"/>
    <use href="#hex" x="2" y="149" width="36" height="40" fill="#5f7d5a"/>
    <use href="#hex" x="41" y="149" width="36" height="40" fill="#c48a5a"/>
    <use href="#hex" x="80" y="149" width="36" height="40" fill="#b85a7a"/>
    <use href="#hex" x="21" y="185" width="36" height="40" fill="#6b6f62"/>
    <use href="#hex" x="60" y="185" width="36" height="40" fill="#c86a78"/>
    <use href="#hex" x="41" y="221" width="36" height="40" fill="#a2564a"/>
  </svg>

  <div class="copy" style="left:133px;top:135px;width:118px">
    <p>Lantern Petals brings the best of professional florists and supermarkets together for the benefit of consumers. It supports a national network of owner-operator franchisees with comprehensive services to enhance franchise profits. Lantern Petals works with some of the country's largest and most progressive supermarkets to provide franchisee ownership and operation of their strategically important floral departments.</p>
    <p>Our franchisees are the cornerstone of our business. Many of them are already professional florists or florist employees who wish to expand their businesses without the significant costs of a traditional flower shop. Others are creative types or flower lovers who have made a career change in order to express their talents and make people happy. Still others are entrepreneurs in search of owning their own business. All are welcome if they meet Lantern Petals' high standards of quality, service and ethical business practices.</p>
  </div>

  <div class="script-head" style="left:27px;top:264px">Opportunity for New Florist Franchisees</div>
  <ul class="ticks" style="left:27px;top:275px;width:150px">
    <li>Be an owner and your own boss while nurturing your creativity</li>
    <li>Attractive earnings potential; paid weekly</li>
    <li>No experience necessary, we set you up to operate and provide extensive support</li>
    <li>Professional training provided, and a path to floral design industry certification</li>
    <li>Low operating and supply costs which leverage supermarket economies</li>
    <li>Affordable franchise fees and low initial investment</li>
    <li>Opportunities to expand to different locations</li>
  </ul>
  <svg class="arrow" style="left:153px;top:304px" viewBox="0 0 20 8" aria-hidden="true"><path d="M1 7 C7 5 12 4 18 2 M14.5 1 L18 2 L15.5 4.5" fill="none" stroke="#333" stroke-width=".7"/></svg>
  <div class="pill" style="left:183px;top:296px;width:62px">NEW FLORIST INQUIRY NOW</div>

  <div class="script-head" style="left:27px;top:345px">Opportunity for Professional Floral Retailers</div>
  <ul class="ticks" style="left:27px;top:356px;width:160px">
    <li>Become a multi-site florist</li>
    <li>Add a high volume, high traffic location</li>
    <li>Enhance customer acquisition for specialty custom events</li>
    <li>Reduce product costs</li>
    <li>Leverage staffing across locations</li>
    <li>Leverage Lantern Petals best-in-class technology, support and marketing across locations</li>
  </ul>
  <svg class="arrow" style="left:180px;top:386px" viewBox="0 0 20 8" aria-hidden="true"><path d="M1 7 C7 5 12 4 18 2 M14.5 1 L18 2 L15.5 4.5" fill="none" stroke="#333" stroke-width=".7"/></svg>
  <div class="pill" style="left:183px;top:372px;width:62px">FLORIST INQUIRY NOW</div>
</section>
<footer class="footer" style="position:absolute;left:630px;top:593px">
  <div class="socials" style="top:3px"><i></i><i></i><i></i><i></i><i></i></div>
  <div class="foot-links" style="top:14px">About Us<span>|</span>For Supermarkets<span>|</span>For Franchisees<span>|</span>Our Gallery<span>|</span>Contact Us</div>
  <div class="foot-copy" style="top:24px">Lantern Petals © 2024 All Rights Reserved | Privacy Policy | Terms and Conditions</div>
</footer>

<!-- OUR GALLERY -->
<section class="page" style="left:24px;top:619px;height:475px">
  <div class="hero">
    <svg viewBox="0 0 271 126">
      <rect role="img" aria-label="Photo of green hydrangeas and roses" width="271" height="126" fill="url(#heroPhoto)"/>
      <path fill="var(--orange)" d="M0 58 C80 42 170 62 271 116 L271 126 L0 126Z"/>
      <path fill="var(--white)" d="M0 104 C90 84 190 106 271 122 L271 126 L0 126Z"/>
      <path fill="var(--green)" d="M0 91 C50 77 100 80 140 97 C100 86 50 88 0 101Z"/>
    </svg>
  </div>
  <div class="logo-tab"><span class="logo-dot"></span><span class="logo-name">Lantern<br>Petals</span></div>
  <div class="menu-btn"><i></i><i></i><i></i></div>
  <div class="hero-kicker" style="top:27px">LANTERN PETALS</div>
  <div class="hero-title" style="top:33px;font-size:25px">Our Gallery</div>

  <div class="band" style="top:280px;height:147px">
    <svg viewBox="0 0 271 172" style="height:147px" preserveAspectRatio="none">
      <rect role="img" aria-label="Photo of pink roses in a flower shop" width="271" height="110" fill="url(#bandPhoto)"/>
      <path fill="var(--orange)" d="M0 52 C70 34 140 58 175 108 C195 138 230 150 271 136 L271 172 L0 172Z"/>
      <path fill="var(--mint)" d="M0 42 C65 22 135 38 172 96 L175 108 C140 58 70 34 0 52Z"/>
      <circle cx="200" cy="88" r="45" fill="var(--white)"/>
    </svg>
    <div class="band-title" style="top:78px">Contact Us</div>
    <div class="band-sub" style="top:102px">For questions and further information.</div>
    <div class="band-mail" style="top:114px">Contact: info@Lantern-Petals.com</div>
    <div class="band-logo" style="top:66px"><span class="logo-dot"></span><span>Lantern<br>Petals</span></div>
  </div>

  <svg class="hexes" viewBox="0 0 271 600" role="img" aria-label="Honeycomb gallery of florist portraits and flower displays">
    <use href="#hex" x="24" y="112" width="38" height="42" fill="#b8a08a"/>
    <use href="#hex" x="64" y="112" width="38" height="42" fill="#7f8e6a"/>
    <use href="#hex" x="105" y="112" width="38" height="42" fill="#8a9a6a"/>
    <use href="#hex" x="3" y="148" width="38" height="42" fill="#5f7d5a"/>
    <use href="#hex" x="44" y="148" width="38" height="42" fill="#c48a5a"/>
    <use href="#hex" x="84" y="148" width="38" height="42" fill="#6a8a5a"/>
    <use href="#hex" x="125" y="148" width="38" height="42" fill="#c86a78"/>
    <use href="#hex" x="165" y="148" width="38" height="42" fill="#a0805a"/>
    <use href="#hex" x="205" y="148" width="38" height="42" fill="#b57a6a"/>
    <use href="#hex" x="24" y="184" width="38" height="42" fill="#6b6f62"/>
    <use href="#hex" x="64" y="184" width="38" height="42" fill="#c0506a"/>
    <use href="#hex" x="105" y="184" width="38" height="42" fill="#d8a0b0"/>
    <use href="#hex" x="145" y="184" width="38" height="42" fill="#8aa0a8"/>
    <use href="#hex" x="184" y="184" width="38" height="42" fill="#5a6e8a"/>
    <use href="#hex" x="225" y="184" width="38" height="42" fill="#c85a6a"/>
    <use href="#hex" x="44" y="219" width="38" height="42" fill="#b0a8a0"/>
    <use href="#hex" x="84" y="219" width="38" height="42" fill="#9a6a52"/>
    <use href="#hex" x="125" y="219" width="38" height="42" fill="#c86a7a"/>
    <use href="#hex" x="165" y="219" width="38" height="42" fill="#6a6a62"/>
    <use href="#hex" x="205" y="219" width="38" height="42" fill="#a2745a"/>
    <use href="#hex" x="145" y="252" width="38" height="42" fill="#9aa86a"/>
    <use href="#hex" x="184" y="252" width="38" height="42" fill="#b88a6a"/>
    <use href="#hex" x="225" y="252" width="38" height="42" fill="#7a8a4a"/>
  </svg>

  <footer class="footer" style="top:427px">
    <div class="socials"><i></i><i></i><i></i><i></i><i></i></div>
    <div class="foot-links">About Us<span>|</span>For Supermarkets<span>|</span>For Franchisees<span>|</span>Our Gallery<span>|</span>Contact Us</div>
    <div class="foot-copy">Lantern Petals © 2024 All Rights Reserved | Privacy Policy | Terms and Conditions</div>
  </footer>
</section>

<!-- CONTACT US -->
<section class="page" style="left:327px;top:619px;height:552px">
  <div class="hero">
    <svg viewBox="0 0 271 126">
      <rect role="img" aria-label="Photo of a florist shop counter filled with green plants" width="271" height="126" fill="url(#heroPhoto)"/>
      <path fill="var(--orange)" d="M0 58 C80 42 170 62 271 116 L271 126 L0 126Z"/>
      <path fill="var(--white)" d="M0 104 C90 84 190 106 271 122 L271 126 L0 126Z"/>
      <path fill="var(--green)" d="M0 91 C50 77 100 80 140 97 C100 86 50 88 0 101Z"/>
    </svg>
  </div>
  <div class="logo-tab"><span class="logo-dot"></span><span class="logo-name">Lantern<br>Petals</span></div>
  <div class="menu-btn"><i></i><i></i><i></i></div>
  <div class="hero-kicker" style="top:27px">LANTERN PETALS</div>
  <div class="hero-title" style="top:33px;font-size:25px">Contact Us</div>

  <div class="band" style="top:333px">
    <svg viewBox="0 0 271 172">
      <rect role="img" aria-label="Photo of pink roses in a flower shop window" width="271" height="110" fill="url(#bandPhoto)"/>
      <path fill="var(--orange)" d="M0 52 C70 34 140 58 175 108 C195 138 230 150 271 136 L271 172 L0 172Z"/>
      <path fill="var(--mint)" d="M0 42 C65 22 135 38 172 96 L175 108 C140 58 70 34 0 52Z"/>
      <circle cx="200" cy="88" r="45" fill="var(--white)"/>
    </svg>
    <div class="band-title">Contact Us</div>
    <div class="band-sub">For questions and further information.</div>
    <div class="band-mail">Contact: info@Lantern-Petals.com</div>
    <div class="band-logo"><span class="logo-dot"></span><span>Lantern<br>Petals</span></div>
  </div>
  <div style="left:0;top:320px;width:271px;height:32px;background:linear-gradient(var(--white) 55%,rgba(255,255,255,0))"></div>

  <div class="form-head" style="left:25px;top:126px">For questions and further information</div>
  <div class="form-mail" style="left:25px;top:143px">Contact: <b>info@Lantern-Petals.com</b></div>
  <div class="pill solid" style="left:25px;top:154px;width:62px">NEW FLORIST FRANCHISE INQUIRY</div>
  <div class="pill" style="left:91px;top:154px;width:86px">PROFESSIONAL FLORIST FRANCHISE INQUIRY</div>

  <div class="field" style="left:25px;top:172px;width:108px">First Name</div>
  <div class="field" style="left:137px;top:172px;width:108px">Last Name</div>
  <div class="field" style="left:25px;top:185px;width:108px">Email</div>
  <div class="field" style="left:137px;top:185px;width:108px">Mobile Phone</div>
  <div class="field" style="left:25px;top:198px;width:220px"><span class="split">Home Address</span><span class="split"># and street</span><span class="split">City</span><span class="split">State</span><span class="split">Post code</span><span class="split">Country</span></div>
  <div class="field" style="left:25px;top:211px;width:108px">Location of Interest</div>
  <div class="field" style="left:137px;top:211px;width:108px">State, City<span class="chev"></span></div>
  <div class="field tall" style="left:25px;top:224px;width:220px">Do you now or have you ever worked for a florist? Please describe.</div>
  <div class="field tall" style="left:25px;top:248px;width:220px">Why are you interested in owning a florist franchise?</div>
  <div class="field" style="left:25px;top:272px;width:220px;height:16px;line-height:4.6px">
    <span>Legal eligibility to work&nbsp; In US?<span class="box on"></span>Yes<span class="box"></span>No<br>
    <span style="padding-left:37px">In UK?</span><span class="box"></span>Yes<span class="box"></span>No</span>
  </div>
  <div class="field" style="left:25px;top:290px;width:220px">Have you ever worked for a franchise?<span style="margin-left:30px"><span class="box on"></span>Yes<span class="box"></span>No</span></div>
  <div class="field" style="left:25px;top:303px;width:220px">Are you willing to relocate?<span style="margin-left:43px"><span class="box on"></span>Yes<span class="box"></span>No</span></div>
  <div class="field" style="left:25px;top:316px;width:220px">How did you hear about Lantern Petals?<span class="chev"></span></div>
  <div class="thanks" style="left:25px;top:328px;width:200px">Thank you for your interest in franchising with Lantern Petals. We look forward to learning more about you and sharing our exciting opportunity with you.</div>
  <div class="pill solid" style="left:183px;top:341px;width:62px;height:10px;border:1px solid #b77a08">SUBMIT NOW</div>

  <footer class="footer" style="top:505px">
    <div class="socials"><i></i><i></i><i></i><i></i><i></i></div>
    <div class="foot-links">About Us<span>|</span>For Supermarkets<span>|</span>For Franchisees<span>|</span>Our Gallery<span>|</span>Contact Us</div>
    <div class="foot-copy">Lantern Petals © 2024 All Rights Reserved | Privacy Policy | Terms and Conditions</div>
  </footer>
</section>

</body>
</html>
```